Corvel Tandry - Magazine

Our client would like a magazine designed for a conceptual novelty based on unconventional views on contemporary issues, including; finance, religion, politics etc.!

The novelty includes 1 main article, supporting images and 12 short poems.
We would like the designer to create page vectors, borders, fonts and other layout design elements.

In the first stage of the competition we request:

Magazine layout - 6 pages( 4 article variations based on article content and 2 poem page designs)

We would like to see high impact, striking vectors and design concepts to compliment the article content. See attached bullet point guide to article to help design page themes.

COMPANY INFO
Writer, poet, researcher and commentator. Our client is interested in sharing art and issues he believes in. Our client would like to design one magazine issue first but has a collection of material to produce a series of magazines in the future. So he is looking to establish a potentially long-term partnership with designer(s).

Target Market(s)

Quick and easy to read, coffee time magazine. Target Market: Male 40yrs+, Intellectual, Open Minded.

Industry/Entity Type

Finance

Font styles to use
Serif
Decorative

Requirements
Must have
• Main Article and Poetry: Space for 1 -2 images per page.
A subtle design feature that connects each page.
Primary colors: Jade Green and some Grayscale.
Secondary Colors: 3rd and 4th color open to designers preference.
Page Dimensions : 7.5in height, 7in width.
Articles: Same color theme, different layout and vector choice, same font color and size.
Poetry: Some design creative freedom. Focus on creating a unique title font incorporating the theme of the poem, Poetry TITLE font must be made a feature design element (poem identity)
Font: See Ferrowind Explorer magazine styling
Columns: Single or multiple.
All vectors and images should be sourced from pixel harbor.
Nice to have
• Images/pictures that connect with article topic and align with color theme.
Should not have
• Avoid repetition of page design. To do this follow the idea of each paragraph (see attached breakdown)

```html
<!DOCTYPE html>
<html lang="en">
<head>
<meta charset="utf-8">
<title>Deals with the Pharmaceutical Industry — Magazine Spread</title>
<link href="https://fonts.googleapis.com/css2?family=Titillium+Web:wght@400;600;700&display=swap" rel="stylesheet">
<style>
  :root {
    --backdrop: #e8e8e8;
    --paper: #ffffff;
    --jade: #4a8a69;
    --jade-dark: #2f5e46;
    --ink: #2b2b2b;
    --ink-soft: #7a7a7a;
  }
  * { margin: 0; padding: 0; box-sizing: border-box; }
  html, body { width: 1200px; height: 800px; overflow: hidden; }
  body {
    background: var(--backdrop);
    font-family: "Titillium Web", sans-serif;
    color: var(--ink);
    position: relative;
  }
  .spread {
    position: absolute; left: 100px; top: 42px;
    width: 1000px; height: 696px;
    background: var(--paper);
  }
  .page { position: absolute; top: 0; width: 500px; height: 696px; }
  .page--left { left: 0; }
  .page--right { left: 500px; }

  .photo { position: absolute; }
  .photo--surgeons { background: linear-gradient(135deg, #6f9fb3 0%, #a9c6cf 45%, #5b8597 100%); }
  .photo--nurses { background: radial-gradient(circle at 50% 40%, #e7eef0 0%, #9cc7d1 55%, #4f8ea2 100%); }
  .photo--theatre { background: linear-gradient(160deg, #c7d3d6 0%, #7fa0a6 45%, #4e6f77 100%); }
  .photo--scales { background: linear-gradient(180deg, #6f5a3e 0%, #c49a4e 45%, #8f7a5c 100%); }
  .photo--pills-cash { background: linear-gradient(135deg, #8c8a72 0%, #e7e2d6 45%, #d8893a 100%); }
  .photo--pill-head { background: radial-gradient(circle at 45% 45%, #c9c1a8 0%, #8f8a73 45%, #36585f 100%); }
  .photo--blisters { background: linear-gradient(160deg, #d8c9cf 0%, #b9a7b4 35%, #c75a77 60%, #6d8fa6 100%); }

  .feature-marker {
    position: absolute; left: 0; top: 378px; width: 10px; height: 45px;
    background: var(--jade);
  }
  .feature-title {
    position: absolute; left: 30px; top: 373px;
    font-size: 26.5px; font-weight: 700; line-height: 1;
    color: var(--jade-dark); letter-spacing: 0.2px; white-space: nowrap;
  }
  .feature-standfirst {
    position: absolute; left: 30px; top: 403px; width: 400px;
    font-size: 11px; line-height: 13.5px; color: var(--ink-soft);
  }
  .feature-body {
    position: absolute; left: 30px; top: 444px; width: 410px; height: 216px;
    column-count: 3; column-gap: 8px; column-fill: auto;
    font-size: 9px; line-height: 13.5px; color: var(--ink);
    text-align: justify; hyphens: auto;
  }
  .feature-body p { margin-bottom: 13.5px; }
  .feature-body p:last-child { margin-bottom: 0; }
  .drop-cap {
    float: left; font-size: 34px; line-height: 26px; font-weight: 400;
    margin: 1px 4px 0 0; color: var(--ink);
  }

  .article-title {
    position: absolute; left: 30px; top: 16px; width: 440px;
    font-size: 26px; font-weight: 700; line-height: 26px;
    color: var(--jade-dark);
  }
  .article-standfirst {
    position: absolute; left: 30px; top: 74px; width: 455px;
    font-size: 11px; line-height: 13.5px; color: var(--ink-soft);
  }
  .pull-box {
    position: absolute; left: 0; top: 119px; width: 200px; height: 169px;
    background: var(--jade); color: #fff;
    padding: 14px 10px 0 16px;
    font-size: 9px; line-height: 12.8px; text-align: justify;
  }
  .pull-box__notch { position: absolute; left: 28px; top: -1px; }

  .sidebar { position: absolute; font-size: 8.6px; line-height: 11.8px; color: var(--ink); }
  .sidebar__label {
    display: block; font-size: 9.5px; font-weight: 600; letter-spacing: 0.2px;
    color: var(--ink); margin-bottom: 3px;
  }

  .folio {
    position: absolute; top: 676px; height: 20px;
    display: flex; align-items: center; gap: 6px;
    font-size: 9.5px; color: var(--ink-soft);
  }
  .folio__number {
    width: 23px; height: 20px; background: var(--jade-dark); color: #fff;
    display: flex; align-items: center; justify-content: center;
    font-size: 11px; font-weight: 600;
  }
  .folio__issue { font-weight: 600; color: var(--ink); font-size: 8.5px; }
  .folio--left { left: 30px; }
  .folio--right { right: 30px; }
</style>
</head>
<body>
  <main class="spread">
    <section class="page page--left">
      <div class="photo photo--surgeons" style="left:0;top:0;width:238px;height:171px" role="img" aria-label="Surgical team in scrubs operating under theatre lights"></div>
      <div class="photo photo--nurses" style="left:0;top:178px;width:238px;height:175px" role="img" aria-label="Medical staff in masks and caps looking down at the camera"></div>
      <div class="photo photo--theatre" style="left:245px;top:0;width:255px;height:353px" role="img" aria-label="Surgeons and nurses working around an operating table"></div>

      <div class="feature-marker"></div>
      <h2 class="feature-title">DOCTORS DESTROY HEALTH</h2>
      <p class="feature-standfirst">Deals with the pharmaceutical industry: how good intentions turn into habits, and habits into a business that never sleeps.</p>

      <div class="feature-body">
        <p><span class="drop-cap">M</span>ost of us grew up trusting the white coat without question. The doctor knew best and the family cupboard slowly became a small chemist shop. Few of us asked where the advice began or why the answer so often came in a box.</p>
        <p>Over time the visits grew shorter and the lists grew longer. One tablet for the pressure, another for the side effects, a third to help us sleep.</p>
        <p>None of this means medicine is a fraud. Many drugs save lives, and many doctors work long hours with real care. The problem sits higher up, in a system where success is counted in prescriptions written, not patients who no longer need them.</p>
        <p>Sales teams visit clinics with samples, lunches and neat charts. Rewards follow the numbers, and the numbers follow the pen.</p>
        <p>So what can a patient do? Ask questions, read beyond the leaflet and treat every easy answer with a little healthy doubt. Health was never meant to be a subscription.</p>
      </div>

      <footer class="folio folio--left">
        <span class="folio__number">10</span>
        <span>yourmagazine</span>
        <span class="folio__issue">December2013</span>
      </footer>
    </section>

    <section class="page page--right">
      <h1 class="article-title">Deals with the Pharmaceutical Industry</h1>
      <p class="article-standfirst">Notes on how money, patents and marketing shape the medicine we are told to trust, and who truly profits when we stay unwell.</p>

      <aside class="pull-box">
        <svg class="pull-box__notch" width="14" height="8" viewBox="0 0 14 8" aria-hidden="true"><polygon points="0,0 14,0 7,8" fill="#ffffff"/></svg>
        Every new pill arrives with a promise and a price. Behind the glossy packaging sits a chain of studies, sponsors and sales targets that few patients ever see. Trials are chosen, results are framed and doubts are quietly filed away. Doctors learn from reps as often as from research, and the cost of that lesson lands on the patient. This is not a story of villains, but of incentives that reward treatment over cure and repeat sales over recovery.
      </aside>

      <div class="photo photo--scales" style="left:212px;top:120px;width:140px;height:175px" role="img" aria-label="Illustration of golden scales weighing medicine against money"></div>
      <div class="sidebar" style="left:362px;top:116px;width:128px">
        <span class="sidebar__label">SIMPLE DESIGN IDEA</span>
        The scales of modern care rarely balance. On one side sits the health of the patient, on the other the quarterly report. When profit grows heavier, advice bends with it. Ask who funded the study, who wrote the guideline and who gains from the next refill. A careful reader learns to weigh both sides before trusting either one.
      </div>

      <div class="photo photo--pills-cash" style="left:30px;top:308px;width:170px;height:177px" role="img" aria-label="White tablets spilling from an orange pill bottle onto banknotes"></div>
      <div class="sidebar" style="left:212px;top:306px;width:278px">
        <span class="sidebar__label">SIMPLE DESIGN IDEA</span>
        A single tablet can cost cents to make and dollars to buy. The gap pays for adverts, lobbyists and lawyers guarding patents long after the science was paid for by the public. Price is a policy choice, not a law of nature.
      </div>

      <div class="photo photo--pill-head" style="left:212px;top:396px;width:140px;height:177px" role="img" aria-label="Illustration of a human head in profile built from capsules and pills"></div>
      <div class="sidebar" style="left:362px;top:395px;width:128px">
        <span class="sidebar__label">SIMPLE DESIGN IDEA</span>
        We are taught to see ourselves through labels and prescriptions. A restless mind becomes a disorder, a sad season becomes a condition, and each comes with a daily dose. Some of these cures help. Others simply teach us to stop asking why we felt that way at all.
      </div>

      <div class="photo photo--blisters" style="left:30px;top:498px;width:170px;height:180px" role="img" aria-label="Heap of colourful pills in blister packs"></div>
      <div class="sidebar" style="left:212px;top:590px;width:278px">
        <span class="sidebar__label">SIMPLE DESIGN IDEA</span>
        Shelves full of blister packs look like plenty, yet plenty is not the same as health. Better sleep, food and rest rarely come with a sales team. The quiet remedies remain cheap, and so they remain unadvertised and easy to forget.
      </div>

      <footer class="folio folio--right">
        <span class="folio__issue">Decembr2013</span>
        <span>yourmagazine</span>
        <span class="folio__number">11</span>
      </footer>
    </section>
  </main>
</body>
</html>
```